Need a website where people can find information about the newly formed Northmere Valuation Oversight Board. Soon after, we will need a place to publish our findings as we audit each municipality in the State of Wisconsin. I have a logo (designed by Artwell Hub), a MS Word document showing the content and a set of images to choose from that we can purchase from Pixmarla.com (found here https://www.pixmarla.com/collaboration/boards/-Xq7TbLwRmNoPzYkAuH-Jd)

```html
<!DOCTYPE html>
<html lang="en">
<head>
<meta charset="utf-8">
<title>Audit Results – NVOB</title>
<link rel="stylesheet" href="https://fonts.googleapis.com/css2?family=Roboto:wght@300;400;500&family=Work+Sans:wght@500;600;800&display=swap">
<style>
  :root {
    --green: #3f8a14;
    --green-text: #3a8a1a;
    --ink: #111111;
    --muted: #555555;
    --cell-alt: #f4f4f4;
    --cell-border: #ececec;
    --white: #ffffff;
    --footer-bg: #131313;
  }
  * { box-sizing: border-box; margin: 0; padding: 0; }
  html, body { width: 894px; height: 1200px; overflow: hidden; background: var(--white); }
  body { position: relative; font-family: "Roboto", sans-serif; }

  .hero { position: absolute; top: 0; left: 0; width: 894px; height: 370px; }
  .hero svg { display: block; }

  .brand {
    position: absolute; top: 30px; left: 83px;
    display: flex; align-items: center; gap: 8px;
  }
  .brand-dot { width: 30px; height: 30px; border-radius: 50%; background: var(--green); }
  .brand-name { font-family: "Work Sans", sans-serif; font-weight: 600; font-size: 17px; color: var(--white); letter-spacing: .5px; }

  .main-nav {
    position: absolute; top: 41px; right: 83px;
    display: flex; gap: 23px;
  }
  .main-nav a {
    font-family: "Roboto", sans-serif; font-weight: 500; font-size: 10.6px;
    color: var(--white); text-decoration: none; text-transform: uppercase;
    padding-bottom: 6px; position: relative;
  }
  .main-nav a.active::after {
    content: ""; position: absolute; left: 0; right: 0; bottom: 0;
    height: 2px; background: var(--white);
  }

  .scroll-down {
    position: absolute; left: 423px; top: 313px; width: 48px; height: 48px;
    border-radius: 50%; background: var(--white);
    box-shadow: 0 2px 6px rgba(0,0,0,.15);
    display: flex; align-items: center; justify-content: center;
  }

  .results { position: absolute; top: 415px; left: 83px; width: 728px; text-align: center; }
  .results h1 { font-family: "Work Sans", sans-serif; font-weight: 800; font-size: 26px; color: var(--ink); letter-spacing: .3px; }
  .results p { margin-top: 16px; font-weight: 300; font-size: 11px; color: var(--muted); }

  .county-grid {
    position: absolute; top: 511px; left: 83px; width: 728px;
    display: grid; grid-template-columns: repeat(6, 1fr); grid-auto-rows: 35.2px;
    list-style: none;
  }
  .county-grid li {
    display: flex; align-items: center; justify-content: center; gap: 6px;
    border: 0.5px solid var(--cell-border);
    font-family: "Work Sans", sans-serif; font-weight: 500; font-size: 10.5px; color: var(--green-text);
  }
  .county-grid li.alt { background: var(--cell-alt); }

  .site-footer { position: absolute; top: 995px; left: 0; width: 894px; height: 205px; }
  .site-footer svg { position: absolute; top: 0; left: 0; }
  .footer-brand {
    position: absolute; top: 80px; left: 0; width: 894px;
    display: flex; justify-content: center; align-items: center; gap: 8px;
  }
  .footer-brand .brand-dot { background: var(--white); width: 26px; height: 26px; }
  .footer-rule { position: absolute; top: 160px; left: 83px; width: 728px; height: 1px; background: #444; }
  .copyright { position: absolute; top: 171px; left: 0; width: 894px; text-align: center; font-size: 10px; color: var(--white); }
  .legal { position: absolute; top: 171px; right: 83px; font-size: 10px; color: var(--white); display: flex; gap: 10px; }
</style>
</head>
<body>

<header class="hero">
  <svg width="894" height="370" viewBox="0 0 894 370">
    <defs>
      <linearGradient id="photoTone" x1="0" y1="0" x2="1" y2="0.3">
        <stop offset="0" stop-color="#4a4d50"/>
        <stop offset="0.45" stop-color="#6e6f70"/>
        <stop offset="0.7" stop-color="#b9b6b2"/>
        <stop offset="1" stop-color="#d6d3cf"/>
      </linearGradient>
    </defs>
    <path d="M0 232 Q447 446 894 232 V234 Q447 462 0 234 Z" fill="var(--green)"/>
    <path d="M0 0 H894 V232 Q447 430 0 232 Z" fill="url(#photoTone)" role="img" aria-label="Photo of a hand holding a pen over a printed ledger beside a calculator keyboard"/>
    <path d="M405 342 A43 43 0 0 1 489 342" fill="none" stroke="var(--white)" stroke-width="1.5"/>
  </svg>
  <div class="brand"><span class="brand-dot"></span><span class="brand-name">NVOB</span></div>
  <nav class="main-nav">
    <a href="#">Home</a>
    <a href="#" class="active">Audit Results</a>
    <a href="#">Recommendations</a>
    <a href="#">Blog</a>
    <a href="#">Contact Us</a>
  </nav>
  <a class="scroll-down" href="#results" aria-label="Scroll down">
    <svg width="16" height="16" viewBox="0 0 16 16"><path d="M8 2 V13 M3 8.5 L8 13.5 L13 8.5" fill="none" stroke="var(--green)" stroke-width="2.6" stroke-linecap="round" stroke-linejoin="round"/></svg>
  </a>
</header>

<section class="results" id="results">
  <h1>AUDIT RESULTS</h1>
  <p>Results are published by County. Click the County of the Municipality you are interested in.</p>
</section>

<ul class="county-grid">
  <li class="alt"><svg width="10" height="11" viewBox="0 0 10 11"><path d="M1 .5H6.5L9 3V10.5H1Z M6.5 .5V3H9 M3 8.5 L5 4 L7 8.5 M3.5 7 H6.5" fill="none" stroke="currentColor" stroke-width=".8"/></svg>Lorum Ipsum</li>
  <li><svg width="10" height="11" viewBox="0 0 10 11"><path d="M1 .5H6.5L9 3V10.5H1Z M6.5 .5V3H9 M3 8.5 L5 4 L7 8.5 M3.5 7 H6.5" fill="none" stroke="currentColor" stroke-width=".8"/></svg>Lorum Ipsum</li>
  <li class="alt"><svg width="10" height="11" viewBox="0 0 10 11"><path d="M1 .5H6.5L9 3V10.5H1Z M6.5 .5V3H9 M3 8.5 L5 4 L7 8.5 M3.5 7 H6.5" fill="none" stroke="currentColor" stroke-width=".8"/></svg>Lorum Ipsum</li>
  <li><svg width="10" height="11" viewBox="0 0 10 11"><path d="M1 .5H6.5L9 3V10.5H1Z M6.5 .5V3H9 M3 8.5 L5 4 L7 8.5 M3.5 7 H6.5" fill="none" stroke="currentColor" stroke-width=".8"/></svg>Lorum Ipsum</li>
  <li class="alt"><svg width="10" height="11" viewBox="0 0 10 11"><path d="M1 .5H6.5L9 3V10.5H1Z M6.5 .5V3H9 M3 8.5 L5 4 L7 8.5 M3.5 7 H6.5" fill="none" stroke="currentColor" stroke-width=".8"/></svg>Lorum Ipsum</li>
  <li><svg width="10" height="11" viewBox="0 0 10 11"><path d="M1 .5H6.5L9 3V10.5H1Z M6.5 .5V3H9 M3 8.5 L5 4 L7 8.5 M3.5 7 H6.5" fill="none" stroke="currentColor" stroke-width=".8"/></svg>Lorum Ipsum</li>

  <li><svg width="10" height="11" viewBox="0 0 10 11"><path d="M1 .5H6.5L9 3V10.5H1Z M6.5 .5V3H9 M3 8.5 L5 4 L7 8.5 M3.5 7 H6.5" fill="none" stroke="currentColor" stroke-width=".8"/></svg>Lorum Ipsum</li>
  <li class="alt"><svg width="10" height="11" viewBox="0 0 10 11"><path d="M1 .5H6.5L9 3V10.5H1Z M6.5 .5V3H9 M3 8.5 L5 4 L7 8.5 M3.5 7 H6.5" fill="none" stroke="currentColor" stroke-width=".8"/></svg>Lorum Ipsum</li>
  <li><svg width="10" height="11" viewBox="0 0 10 11"><path d="M1 .5H6.5L9 3V10.5H1Z M6.5 .5V3H9 M3 8.5 L5 4 L7 8.5 M3.5 7 H6.5" fill="none" stroke="currentColor" stroke-width=".8"/></svg>Lorum Ipsum</li>
  <li class="alt"><svg width="10" height="11" viewBox="0 0 10 11"><path d="M1 .5H6.5L9 3V10.5H1Z M6.5 .5V3H9 M3 8.5 L5 4 L7 8.5 M3.5 7 H6.5" fill="none" stroke="currentColor" stroke-width=".8"/></svg>Lorum Ipsum</li>
  <li><svg width="10" height="11" viewBox="0 0 10 11"><path d="M1 .5H6.5L9 3V10.5H1Z M6.5 .5V3H9 M3 8.5 L5 4 L7 8.5 M3.5 7 H6.5" fill="none" stroke="currentColor" stroke-width=".8"/></svg>Lorum Ipsum</li>
  <li class="alt"><svg width="10" height="11" viewBox="0 0 10 11"><path d="M1 .5H6.5L9 3V10.5H1Z M6.5 .5V3H9 M3 8.5 L5 4 L7 8.5 M3.5 7 H6.5" fill="none" stroke="currentColor" stroke-width=".8"/></svg>Lorum Ipsum</li>

  <li class="alt"><svg width="10" height="11" viewBox="0 0 10 11"><path d="M1 .5H6.5L9 3V10.5H1Z M6.5 .5V3H9 M3 8.5 L5 4 L7 8.5 M3.5 7 H6.5" fill="none" stroke="currentColor" stroke-width=".8"/></svg>Lorum Ipsum</li>
  <li><svg width="10" height="11" viewBox="0 0 10 11"><path d="M1 .5H6.5L9 3V10.5H1Z M6.5 .5V3H9 M3 8.5 L5 4 L7 8.5 M3.5 7 H6.5" fill="none" stroke="currentColor" stroke-width=".8"/></svg>Lorum Ipsum</li>
  <li class="alt"><svg width="10" height="11" viewBox="0 0 10 11"><path d="M1 .5H6.5L9 3V10.5H1Z M6.5 .5V3H9 M3 8.5 L5 4 L7 8.5 M3.5 7 H6.5" fill="none" stroke="currentColor" stroke-width=".8"/></svg>Lorum Ipsum</li>
  <li><svg width="10" height="11" viewBox="0 0 10 11"><path d="M1 .5H6.5L9 3V10.5H1Z M6.5 .5V3H9 M3 8.5 L5 4 L7 8.5 M3.5 7 H6.5" fill="none" stroke="currentColor" stroke-width=".8"/></svg>Lorum Ipsum</li>
  <li class="alt"><svg width="10" height="11" viewBox="0 0 10 11"><path d="M1 .5H6.5L9 3V10.5H1Z M6.5 .5V3H9 M3 8.5 L5 4 L7 8.5 M3.5 7 H6.5" fill="none" stroke="currentColor" stroke-width=".8"/></svg>Lorum Ipsum</li>
  <li><svg width="10" height="11" viewBox="0 0 10 11"><path d="M1 .5H6.5L9 3V10.5H1Z M6.5 .5V3H9 M3 8.5 L5 4 L7 8.5 M3.5 7 H6.5" fill="none" stroke="currentColor" stroke-width=".8"/></svg>Lorum Ipsum</li>

  <li><svg width="10" height="11" viewBox="0 0 10 11"><path d="M1 .5H6.5L9 3V10.5H1Z M6.5 .5V3H9 M3 8.5 L5 4 L7 8.5 M3.5 7 H6.5" fill="none" stroke="currentColor" stroke-width=".8"/></svg>Lorum Ipsum</li>
  <li class="alt"><svg width="10" height="11" viewBox="0 0 10 11"><path d="M1 .5H6.5L9 3V10.5H1Z M6.5 .5V3H9 M3 8.5 L5 4 L7 8.5 M3.5 7 H6.5" fill="none" stroke="currentColor" stroke-width=".8"/></svg>Lorum Ipsum</li>
  <li><svg width="10" height="11" viewBox="0 0 10 11"><path d="M1 .5H6.5L9 3V10.5H1Z M6.5 .5V3H9 M3 8.5 L5 4 L7 8.5 M3.5 7 H6.5" fill="none" stroke="currentColor" stroke-width=".8"/></svg>Lorum Ipsum</li>
  <li class="alt"><svg width="10" height="11" viewBox="0 0 10 11"><path d="M1 .5H6.5L9 3V10.5H1Z M6.5 .5V3H9 M3 8.5 L5 4 L7 8.5 M3.5 7 H6.5" fill="none" stroke="currentColor" stroke-width=".8"/></svg>Lorum Ipsum</li>
  <li><svg width="10" height="11" viewBox="0 0 10 11"><path d="M1 .5H6.5L9 3V10.5H1Z M6.5 .5V3H9 M3 8.5 L5 4 L7 8.5 M3.5 7 H6.5" fill="none" stroke="currentColor" stroke-width=".8"/></svg>Lorum Ipsum</li>
  <li class="alt"><svg width="10" height="11" viewBox="0 0 10 11"><path d="M1 .5H6.5L9 3V10.5H1Z M6.5 .5V3H9 M3 8.5 L5 4 L7 8.5 M3.5 7 H6.5" fill="none" stroke="currentColor" stroke-width=".8"/></svg>Lorum Ipsum</li>

  <li class="alt"><svg width="10" height="11" viewBox="0 0 10 11"><path d="M1 .5H6.5L9 3V10.5H1Z M6.5 .5V3H9 M3 8.5 L5 4 L7 8.5 M3.5 7 H6.5" fill="none" stroke="currentColor" stroke-width=".8"/></svg>Lorum Ipsum</li>
  <li><svg width="10" height="11" viewBox="0 0 10 11"><path d="M1 .5H6.5L9 3V10.5H1Z M6.5 .5V3H9 M3 8.5 L5 4 L7 8.5 M3.5 7 H6.5" fill="none" stroke="currentColor" stroke-width=".8"/></svg>Lorum Ipsum</li>
  <li class="alt"><svg width="10" height="11" viewBox="0 0 10 11"><path d="M1 .5H6.5L9 3V10.5H1Z M6.5 .5V3H9 M3 8.5 L5 4 L7 8.5 M3.5 7 H6.5" fill="none" stroke="currentColor" stroke-width=".8"/></svg>Lorum Ipsum</li>
  <li><svg width="10" height="11" viewBox="0 0 10 11"><path d="M1 .5H6.5L9 3V10.5H1Z M6.5 .5V3H9 M3 8.5 L5 4 L7 8.5 M3.5 7 H6.5" fill="none" stroke="currentColor" stroke-width=".8"/></svg>Lorum Ipsum</li>
  <li class="alt"><svg width="10" height="11" viewBox="0 0 10 11"><path d="M1 .5H6.5L9 3V10.5H1Z M6.5 .5V3H9 M3 8.5 L5 4 L7 8.5 M3.5 7 H6.5" fill="none" stroke="currentColor" stroke-width=".8"/></svg>Lorum Ipsum</li>
  <li><svg width="10" height="11" viewBox="0 0 10 11"><path d="M1 .5H6.5L9 3V10.5H1Z M6.5 .5V3H9 M3 8.5 L5 4 L7 8.5 M3.5 7 H6.5" fill="none" stroke="currentColor" stroke-width=".8"/></svg>Lorum Ipsum</li>

  <li><svg width="10" height="11" viewBox="0 0 10 11"><path d="M1 .5H6.5L9 3V10.5H1Z M6.5 .5V3H9 M3 8.5 L5 4 L7 8.5 M3.5 7 H6.5" fill="none" stroke="currentColor" stroke-width=".8"/></svg>Lorum Ipsum</li>
  <li class="alt"><svg width="10" height="11" viewBox="0 0 10 11"><path d="M1 .5H6.5L9 3V10.5H1Z M6.5 .5V3H9 M3 8.5 L5 4 L7 8.5 M3.5 7 H6.5" fill="none" stroke="currentColor" stroke-width=".8"/></svg>Lorum Ipsum</li>
  <li><svg width="10" height="11" viewBox="0 0 10 11"><path d="M1 .5H6.5L9 3V10.5H1Z M6.5 .5V3H9 M3 8.5 L5 4 L7 8.5 M3.5 7 H6.5" fill="none" stroke="currentColor" stroke-width=".8"/></svg>Lorum Ipsum</li>
  <li class="alt"><svg width="10" height="11" viewBox="0 0 10 11"><path d="M1 .5H6.5L9 3V10.5H1Z M6.5 .5V3H9 M3 8.5 L5 4 L7 8.5 M3.5 7 H6.5" fill="none" stroke="currentColor" stroke-width=".8"/></svg>Lorum Ipsum</li>
  <li><svg width="10" height="11" viewBox="0 0 10 11"><path d="M1 .5H6.5L9 3V10.5H1Z M6.5 .5V3H9 M3 8.5 L5 4 L7 8.5 M3.5 7 H6.5" fill="none" stroke="currentColor" stroke-width=".8"/></svg>Lorum Ipsum</li>
  <li class="alt"><svg width="10" height="11" viewBox="0 0 10 11"><path d="M1 .5H6.5L9 3V10.5H1Z M6.5 .5V3H9 M3 8.5 L5 4 L7 8.5 M3.5 7 H6.5" fill="none" stroke="currentColor" stroke-width=".8"/></svg>Lorum Ipsum</li>

  <li class="alt"><svg width="10" height="11" viewBox="0 0 10 11"><path d="M1 .5H6.5L9 3V10.5H1Z M6.5 .5V3H9 M3 8.5 L5 4 L7 8.5 M3.5 7 H6.5" fill="none" stroke="currentColor" stroke-width=".8"/></svg>Lorum Ipsum</li>
  <li><svg width="10" height="11" viewBox="0 0 10 11"><path d="M1 .5H6.5L9 3V10.5H1Z M6.5 .5V3H9 M3 8.5 L5 4 L7 8.5 M3.5 7 H6.5" fill="none" stroke="currentColor" stroke-width=".8"/></svg>Lorum Ipsum</li>
  <li class="alt"><svg width="10" height="11" viewBox="0 0 10 11"><path d="M1 .5H6.5L9 3V10.5H1Z M6.5 .5V3H9 M3 8.5 L5 4 L7 8.5 M3.5 7 H6.5" fill="none" stroke="currentColor" stroke-width=".8"/></svg>Lorum Ipsum</li>
  <li><svg width="10" height="11" viewBox="0 0 10 11"><path d="M1 .5H6.5L9 3V10.5H1Z M6.5 .5V3H9 M3 8.5 L5 4 L7 8.5 M3.5 7 H6.5" fill="none" stroke="currentColor" stroke-width=".8"/></svg>Lorum Ipsum</li>
  <li class="alt"><svg width="10" height="11" viewBox="0 0 10 11"><path d="M1 .5H6.5L9 3V10.5H1Z M6.5 .5V3H9 M3 8.5 L5 4 L7 8.5 M3.5 7 H6.5" fill="none" stroke="currentColor" stroke-width=".8"/></svg>Lorum Ipsum</li>
  <li><svg width="10" height="11" viewBox="0 0 10 11"><path d="M1 .5H6.5L9 3V10.5H1Z M6.5 .5V3H9 M3 8.5 L5 4 L7 8.5 M3.5 7 H6.5" fill="none" stroke="currentColor" stroke-width=".8"/></svg>Lorum Ipsum</li>

  <li><svg width="10" height="11" viewBox="0 0 10 11"><path d="M1 .5H6.5L9 3V10.5H1Z M6.5 .5V3H9 M3 8.5 L5 4 L7 8.5 M3.5 7 H6.5" fill="none" stroke="currentColor" stroke-width=".8"/></svg>Lorum Ipsum</li>
  <li class="alt"><svg width="10" height="11" viewBox="0 0 10 11"><path d="M1 .5H6.5L9 3V10.5H1Z M6.5 .5V3H9 M3 8.5 L5 4 L7 8.5 M3.5 7 H6.5" fill="none" stroke="currentColor" stroke-width=".8"/></svg>Lorum Ipsum</li>
  <li><svg width="10" height="11" viewBox="0 0 10 11"><path d="M1 .5H6.5L9 3V10.5H1Z M6.5 .5V3H9 M3 8.5 L5 4 L7 8.5 M3.5 7 H6.5" fill="none" stroke="currentColor" stroke-width=".8"/></svg>Lorum Ipsum</li>
  <li class="alt"><svg width="10" height="11" viewBox="0 0 10 11"><path d="M1 .5H6.5L9 3V10.5H1Z M6.5 .5V3H9 M3 8.5 L5 4 L7 8.5 M3.5 7 H6.5" fill="none" stroke="currentColor" stroke-width=".8"/></svg>Lorum Ipsum</li>
  <li><svg width="10" height="11" viewBox="0 0 10 11"><path d="M1 .5H6.5L9 3V10.5H1Z M6.5 .5V3H9 M3 8.5 L5 4 L7 8.5 M3.5 7 H6.5" fill="none" stroke="currentColor" stroke-width=".8"/></svg>Lorum Ipsum</li>
  <li class="alt"><svg width="10" height="11" viewBox="0 0 10 11"><path d="M1 .5H6.5L9 3V10.5H1Z M6.5 .5V3H9 M3 8.5 L5 4 L7 8.5 M3.5 7 H6.5" fill="none" stroke="currentColor" stroke-width=".8"/></svg>Lorum Ipsum</li>

  <li class="alt"><svg width="10" height="11" viewBox="0 0 10 11"><path d="M1 .5H6.5L9 3V10.5H1Z M6.5 .5V3H9 M3 8.5 L5 4 L7 8.5 M3.5 7 H6.5" fill="none" stroke="currentColor" stroke-width=".8"/></svg>Lorum Ipsum</li>
  <li><svg width="10" height="11" viewBox="0 0 10 11"><path d="M1 .5H6.5L9 3V10.5H1Z M6.5 .5V3H9 M3 8.5 L5 4 L7 8.5 M3.5 7 H6.5" fill="none" stroke="currentColor" stroke-width=".8"/></svg>Lorum Ipsum</li>
  <li class="alt"><svg width="10" height="11" viewBox="0 0 10 11"><path d="M1 .5H6.5L9 3V10.5H1Z M6.5 .5V3H9 M3 8.5 L5 4 L7 8.5 M3.5 7 H6.5" fill="none" stroke="currentColor" stroke-width=".8"/></svg>Lorum Ipsum</li>
  <li><svg width="10" height="11" viewBox="0 0 10 11"><path d="M1 .5H6.5L9 3V10.5H1Z M6.5 .5V3H9 M3 8.5 L5 4 L7 8.5 M3.5 7 H6.5" fill="none" stroke="currentColor" stroke-width=".8"/></svg>Lorum Ipsum</li>
  <li class="alt"><svg width="10" height="11" viewBox="0 0 10 11"><path d="M1 .5H6.5L9 3V10.5H1Z M6.5 .5V3H9 M3 8.5 L5 4 L7 8.5 M3.5 7 H6.5" fill="none" stroke="currentColor" stroke-width=".8"/></svg>Lorum Ipsum</li>
  <li><svg width="10" height="11" viewBox="0 0 10 11"><path d="M1 .5H6.5L9 3V10.5H1Z M6.5 .5V3H9 M3 8.5 L5 4 L7 8.5 M3.5 7 H6.5" fill="none" stroke="currentColor" stroke-width=".8"/></svg>Lorum Ipsum</li>

  <li><svg width="10" height="11" viewBox="0 0 10 11"><path d="M1 .5H6.5L9 3V10.5H1Z M6.5 .5V3H9 M3 8.5 L5 4 L7 8.5 M3.5 7 H6.5" fill="none" stroke="currentColor" stroke-width=".8"/></svg>Lorum Ipsum</li>
  <li class="alt"><svg width="10" height="11" viewBox="0 0 10 11"><path d="M1 .5H6.5L9 3V10.5H1Z M6.5 .5V3H9 M3 8.5 L5 4 L7 8.5 M3.5 7 H6.5" fill="none" stroke="currentColor" stroke-width=".8"/></svg>Lorum Ipsum</li>
  <li><svg width="10" height="11" viewBox="0 0 10 11"><path d="M1 .5H6.5L9 3V10.5H1Z M6.5 .5V3H9 M3 8.5 L5 4 L7 8.5 M3.5 7 H6.5" fill="none" stroke="currentColor" stroke-width=".8"/></svg>Lorum Ipsum</li>
  <li class="alt"><svg width="10" height="11" viewBox="0 0 10 11"><path d="M1 .5H6.5L9 3V10.5H1Z M6.5 .5V3H9 M3 8.5 L5 4 L7 8.5 M3.5 7 H6.5" fill="none" stroke="currentColor" stroke-width=".8"/></svg>Lorum Ipsum</li>
  <li><svg width="10" height="11" viewBox="0 0 10 11"><path d="M1 .5H6.5L9 3V10.5H1Z M6.5 .5V3H9 M3 8.5 L5 4 L7 8.5 M3.5 7 H6.5" fill="none" stroke="currentColor" stroke-width=".8"/></svg>Lorum Ipsum</li>
  <li class="alt"><svg width="10" height="11" viewBox="0 0 10 11"><path d="M1 .5H6.5L9 3V10.5H1Z M6.5 .5V3H9 M3 8.5 L5 4 L7 8.5 M3.5 7 H6.5" fill="none" stroke="currentColor" stroke-width=".8"/></svg>Lorum Ipsum</li>

  <li class="alt"><svg width="10" height="11" viewBox="0 0 10 11"><path d="M1 .5H6.5L9 3V10.5H1Z M6.5 .5V3H9 M3 8.5 L5 4 L7 8.5 M3.5 7 H6.5" fill="none" stroke="currentColor" stroke-width=".8"/></svg>Lorum Ipsum</li>
  <li><svg width="10" height="11" viewBox="0 0 10 11"><path d="M1 .5H6.5L9 3V10.5H1Z M6.5 .5V3H9 M3 8.5 L5 4 L7 8.5 M3.5 7 H6.5" fill="none" stroke="currentColor" stroke-width=".8"/></svg>Lorum Ipsum</li>
  <li class="alt"><svg width="10" height="11" viewBox="0 0 10 11"><path d="M1 .5H6.5L9 3V10.5H1Z M6.5 .5V3H9 M3 8.5 L5 4 L7 8.5 M3.5 7 H6.5" fill="none" stroke="currentColor" stroke-width=".8"/></svg>Lorum Ipsum</li>
  <li><svg width="10" height="11" viewBox="0 0 10 11"><path d="M1 .5H6.5L9 3V10.5H1Z M6.5 .5V3H9 M3 8.5 L5 4 L7 8.5 M3.5 7 H6.5" fill="none" stroke="currentColor" stroke-width=".8"/></svg>Lorum Ipsum</li>
  <li class="alt"><svg width="10" height="11" viewBox="0 0 10 11"><path d="M1 .5H6.5L9 3V10.5H1Z M6.5 .5V3H9 M3 8.5 L5 4 L7 8.5 M3.5 7 H6.5" fill="none" stroke="currentColor" stroke-width=".8"/></svg>Lorum Ipsum</li>
  <li><svg width="10" height="11" viewBox="0 0 10 11"><path d="M1 .5H6.5L9 3V10.5H1Z M6.5 .5V3H9 M3 8.5 L5 4 L7 8.5 M3.5 7 H6.5" fill="none" stroke="currentColor" stroke-width=".8"/></svg>Lorum Ipsum</li>

  <li><svg width="10" height="11" viewBox="0 0 10 11"><path d="M1 .5H6.5L9 3V10.5H1Z M6.5 .5V3H9 M3 8.5 L5 4 L7 8.5 M3.5 7 H6.5" fill="none" stroke="currentColor" stroke-width=".8"/></svg>Lorum Ipsum</li>
  <li class="alt"><svg width="10" height="11" viewBox="0 0 10 11"><path d="M1 .5H6.5L9 3V10.5H1Z M6.5 .5V3H9 M3 8.5 L5 4 L7 8.5 M3.5 7 H6.5" fill="none" stroke="currentColor" stroke-width=".8"/></svg>Lorum Ipsum</li>
  <li><svg width="10" height="11" viewBox="0 0 10 11"><path d="M1 .5H6.5L9 3V10.5H1Z M6.5 .5V3H9 M3 8.5 L5 4 L7 8.5 M3.5 7 H6.5" fill="none" stroke="currentColor" stroke-width=".8"/></svg>Lorum Ipsum</li>
  <li class="alt"><svg width="10" height="11" viewBox="0 0 10 11"><path d="M1 .5H6.5L9 3V10.5H1Z M6.5 .5V3H9 M3 8.5 L5 4 L7 8.5 M3.5 7 H6.5" fill="none" stroke="currentColor" stroke-width=".8"/></svg>Lorum Ipsum</li>
  <li><svg width="10" height="11" viewBox="0 0 10 11"><path d="M1 .5H6.5L9 3V10.5H1Z M6.5 .5V3H9 M3 8.5 L5 4 L7 8.5 M3.5 7 H6.5" fill="none" stroke="currentColor" stroke-width=".8"/></svg>Lorum Ipsum</li>
  <li class="alt"><svg width="10" height="11" viewBox="0 0 10 11"><path d="M1 .5H6.5L9 3V10.5H1Z M6.5 .5V3H9 M3 8.5 L5 4 L7 8.5 M3.5 7 H6.5" fill="none" stroke="currentColor" stroke-width=".8"/></svg>Lorum Ipsum</li>
</ul>

<footer class="site-footer">
  <svg width="894" height="205" viewBox="0 0 894 205">
    <path d="M0 120 Q447 -116 894 120 V205 H0 Z" fill="var(--green)"/>
    <path d="M0 124 Q447 -92 894 124 V205 H0 Z" fill="var(--footer-bg)"/>
  </svg>
  <div class="footer-brand"><span class="brand-dot"></span><span class="brand-name">NVOB</span></div>
  <div class="footer-rule"></div>
  <p class="copyright">© 2022 NVOB &nbsp;|&nbsp; All Rights Reserved</p>
  <p class="legal"><span>Privacy Policy</span><span>|</span><span>Terms &amp; Conditions</span></p>
</footer>

</body>
</html>
```